Real Estate Webpage Design

We have an existing website: ferndaleestatecollective.com.au
We focus customised service mainly on Property Management and second-hand property sales.
We are not entirely happy about the current design and layout can stay roughly the same as the back end coding is linked to a CRM system.
We would like to see the design are more reachable to our clients and appearing.
Please check our Website Design Draft for more details.

Industry/Entity Type

Real estate Agency

Number of Pages Required

5+ page

Font styles to use
Sans Serif

Colors

Designer to choose colors to be used in the design.

```html
<!DOCTYPE html>
<html lang="en">
<head>
<meta charset="utf-8">
<title>Ferndale Estate Collective</title>
<link href="https://fonts.googleapis.com/css2?family=Poppins:wght@300;400;500;600&display=swap" rel="stylesheet">
<style>
:root{
  --gold:#E9B94F;
  --navy:#1D2E4C;
  --navy-deep:#172540;
  --ink:#1F2A3C;
  --muted:#8A8F99;
  --line:#E4E6EA;
  --white:#FFFFFF;
}
*{box-sizing:border-box;margin:0;padding:0}
html,body{width:1200px;height:3686px;overflow:hidden}
body{font-family:'Poppins',sans-serif;color:var(--ink);background:var(--white)}
.page{position:relative;width:1200px;height:3686px;overflow:hidden}
.abs{position:absolute}
.photo{position:absolute}

/* header + hero */
.hero{position:absolute;left:0;top:0;width:1200px;height:637px;background:linear-gradient(180deg,#3C4656 0%,#2C3544 45%,#3A4350 75%,#4B5563 100%)}
.hero-shade{position:absolute;inset:0;background:linear-gradient(180deg,rgba(20,28,40,.35),rgba(20,28,40,.15) 50%,rgba(20,28,40,.45))}
.brand{position:absolute;left:60px;top:16px;display:flex;align-items:center;gap:12px}
.brand-mark{width:58px;height:58px;border:3px solid var(--gold)}
.brand-name{font-size:40px;font-weight:500;color:var(--gold);line-height:1}
.brand-sub{font-size:11px;color:var(--gold);letter-spacing:1px;margin-top:2px}
.nav{position:absolute;top:32px;left:413px;display:flex;gap:24px;font-size:14px;color:var(--white)}
.nav .active{color:var(--gold)}
.btn-add{position:absolute;left:990px;top:23px;width:150px;height:37px;background:var(--gold);color:var(--white);font-size:14px;font-weight:500;display:flex;align-items:center;justify-content:center}
.hero-title{position:absolute;top:220px;width:1200px;text-align:center;font-size:40px;font-weight:600;color:var(--gold)}
.hero-text{position:absolute;top:273px;left:260px;width:680px;text-align:center;font-size:13.5px;line-height:23px;color:var(--white)}
.tab{position:absolute;top:359px;height:41px;display:flex;align-items:center;justify-content:center;font-size:14px;color:var(--white)}
.tab.rent{left:502px;width:93px;background:var(--gold)}
.tab.sale{left:595px;width:105px;background:var(--navy)}
.search{position:absolute;left:240px;top:425px;width:718px;height:67px;background:rgba(255,255,255,.92);outline:6px solid rgba(255,255,255,.35)}
.select{position:absolute;top:14px;height:38px;border:1px solid #8D939C;font-size:12px;color:var(--muted);display:flex;align-items:center;justify-content:space-between;padding:0 10px}
.btn-search{position:absolute;left:607px;top:18px;width:89px;height:31px;background:var(--gold);color:var(--white);font-size:14px;display:flex;align-items:center;justify-content:center}

/* section headings */
.eyebrow{font-size:13px;color:var(--gold)}
.heading{font-size:28px;font-weight:500;color:var(--ink)}
.center{position:absolute;width:1200px;text-align:center}

/* listings */
.filters{position:absolute;top:811px;left:293px;display:flex;gap:14px}
.filter{height:37px;border:1px solid var(--ink);font-size:13px;display:flex;align-items:center;justify-content:center}
.filter.on{background:var(--gold);border-color:var(--gold);color:var(--white)}
.card{position:absolute;top:877px;width:340px;height:415px;background:var(--white);box-shadow:0 2px 12px rgba(0,0,0,.09)}
.card-img{position:absolute;left:9px;top:12px;width:322px;height:178px}
.badge{position:absolute;left:0;top:5px;background:var(--ink);color:var(--white);font-size:12px;padding:3px 10px}
.fav{position:absolute;right:16px;top:16px}
.card h3{position:absolute;left:22px;top:192px;font-size:17px;font-weight:500}
.addr{position:absolute;left:22px;top:222px;font-size:13px;display:flex;gap:6px;align-items:center}
.feats{position:absolute;left:22px;top:256px;display:flex;gap:20px;font-size:13px}
.feat{display:flex;gap:10px;align-items:center}
.insp{position:absolute;left:22px;top:296px;font-size:16px;font-weight:500}
.insp-time{position:absolute;left:22px;top:324px;font-size:13px;color:var(--gold)}
.card-foot{position:absolute;left:0;right:0;top:363px;border-top:1px solid var(--line);height:52px}
.agent{position:absolute;left:18px;top:14px;display:flex;align-items:center;gap:12px;font-size:13px}
.avatar{width:29px;height:29px;background:#9CA3AF}
.actions{position:absolute;right:16px;top:20px;display:flex;gap:10px}

/* about / why */
.body-copy{font-size:13.5px;line-height:22.5px;color:var(--muted);font-weight:300}
.btn-outline{position:absolute;width:112px;height:38px;background:var(--gold);border:1px solid #C9972F;color:var(--white);font-size:14px;display:flex;align-items:center;justify-content:center}

/* testimonials */
.testi{position:absolute;left:0;top:2216px;width:1200px;height:431px;background:linear-gradient(180deg,#1F3152,#1B2C4A 60%,#22355A)}
.quote-card{position:absolute;top:164px;width:405px;height:192px;background:rgba(18,30,52,.85);text-align:center;padding:18px 22px 0}
.quote-card p{font-size:14px;line-height:22.5px;color:var(--white);font-weight:300}
.quote-card .who{margin-top:12px;font-size:13.5px;color:var(--gold)}
.qmark{position:absolute;left:16px;top:8px}
.arrow{position:absolute;top:2460px;width:33px;height:33px;display:flex;align-items:center;justify-content:center}

/* news */
.post{position:absolute;top:2806px;width:340px}
.post-img{width:340px;height:206px}
.meta{margin-top:12px;display:flex;gap:16px;font-size:12px;color:var(--muted);align-items:center}
.meta span{display:flex;gap:6px;align-items:center}
.post h4{margin-top:8px;font-size:17px;font-weight:600}
.post p{margin-top:6px;font-size:13.5px;line-height:22px;color:var(--muted);font-weight:300}
.more{margin-top:12px;font-size:13px;color:var(--gold)}

/* footer */
.footer{position:absolute;left:0;top:3341px;width:1200px;height:345px;background:var(--navy)}
.cta{position:absolute;left:60px;top:3237px;width:1080px;height:130px;background:var(--gold)}
.cta h2{position:absolute;left:33px;top:28px;font-size:23px;line-height:38px;font-weight:500;color:var(--navy)}
.cta-btn{position:absolute;left:792px;top:46px;width:168px;height:37px;background:var(--white);border:1px solid var(--navy);font-size:14px;display:flex;align-items:center;justify-content:center}
.f-title{font-size:14px;font-weight:500;color:var(--gold)}
.f-list{list-style:none;font-size:12.5px;color:var(--white);line-height:27.5px;margin-top:14px}
.f-list .active{color:var(--gold)}
.f-text{font-size:12.5px;line-height:21px;color:var(--white)}
.social{display:flex;gap:18px;margin-top:22px}
.social span{width:36px;height:36px;border-radius:50%;border:2px solid var(--gold);display:block}
.social span.fill{background:var(--gold)}
.legal{position:absolute;left:0;top:3649px;width:1200px;height:37px;background:var(--gold);font-size:12px;color:var(--navy)}
</style>
</head>
<body>
<div class="page">

  <!-- HERO -->
  <section class="hero">
    <div class="photo" style="inset:0;background:radial-gradient(ellipse at 50% 40%,#5A6474 0%,#36404F 55%,#262E3B 100%)" role="img" aria-label="Modern multi-storey house at dusk beside a reflecting pool, framed by trees"></div>
    <div class="hero-shade"></div>
    <div class="brand">
      <div class="brand-mark"></div>
      <div><div class="brand-name">Ferndale</div><div class="brand-sub">Estate Collective</div></div>
    </div>
    <nav class="nav">
      <span class="active">Home</span><span>About Us</span><span>Leasing</span><span>Buy</span><span>Sell</span><span>Our Team</span><span>Blog</span><span>Contact Us</span>
    </nav>
    <div class="btn-add">Add Properties</div>
    <h1 class="hero-title">Welcome To Ferndale Estate Collective</h1>
    <p class="hero-text">Lorem Ipsum is simply dummy text of the printing and typesetting industry. Lorem Ipsum has been the industry's standard dummy text ever since the 1500s, when an unknown printer</p>
    <div class="tab rent">Rent</div>
    <div class="tab sale">Sale</div>
    <div class="search">
      <div class="select" style="left:22px;width:174px">Property Category <svg width="16" height="10" viewBox="0 0 16 10"><path d="M1 1l7 7 7-7" fill="none" stroke="#1F2A3C" stroke-width="2"/></svg></div>
      <div class="select" style="left:210px;width:174px">Property City <svg width="16" height="10" viewBox="0 0 16 10"><path d="M1 1l7 7 7-7" fill="none" stroke="#1F2A3C" stroke-width="2"/></svg></div>
      <div class="select" style="left:398px;width:174px">Property Area <svg width="16" height="10" viewBox="0 0 16 10"><path d="M1 1l7 7 7-7" fill="none" stroke="#1F2A3C" stroke-width="2"/></svg></div>
      <div class="btn-search">Search</div>
    </div>
  </section>

  <!-- LISTINGS -->
  <div class="center eyebrow" style="top:719px">Our Properties</div>
  <h2 class="center heading" style="top:745px">Listings Available For Latest Property</h2>
  <div class="filters">
    <div class="filter on" style="width:105px">For Sale</div>
    <div class="filter" style="width:105px">For Lease</div>
    <div class="filter" style="width:105px">Open Times</div>
    <div class="filter" style="width:105px">Sold</div>
    <div class="filter" style="width:105px">Leased</div>
  </div>

  <article class="card" style="left:60px">
    <div class="card-img" style="background:linear-gradient(160deg,#7FB2E0,#C9CED6 55%,#4E6A3A)" role="img" aria-label="Apartment tower with coloured balconies and trees"></div>
    <div class="badge">On Sale</div>
    <svg class="fav" width="18" height="18" viewBox="0 0 24 24"><path d="M12 2l3 7 7 .6-5.3 4.6 1.7 7.3L12 17.6 5.6 21.5l1.7-7.3L2 9.6 9 9z" fill="#E9B94F"/></svg>
    <h3>Kenbury</h3>
    <div class="addr"><svg width="14" height="18" viewBox="0 0 14 18"><path d="M7 1a6 6 0 00-6 6c0 4.5 6 10 6 10s6-5.5 6-10a6 6 0 00-6-6z" fill="none" stroke="#E9B94F" stroke-width="1.3"/><circle cx="7" cy="7" r="2" fill="none" stroke="#E9B94F" stroke-width="1.3"/></svg>18/40 Wattle Street Kenbury...</div>
    <div class="feats">
      <span class="feat"><svg width="22" height="16" viewBox="0 0 22 16"><path d="M1 15V3M21 15V9H1M4 9V5h7v4" fill="none" stroke="#E9B94F" stroke-width="1.3"/></svg>1</span>
      <span class="feat"><svg width="22" height="16" viewBox="0 0 22 16"><path d="M1 8h20v3a4 4 0 01-4 4H5a4 4 0 01-4-4zM4 8V2h3" fill="none" stroke="#E9B94F" stroke-width="1.3"/></svg>1</span>
      <span class="feat"><svg width="26" height="14" viewBox="0 0 26 14"><path d="M1 10V7l4-1 4-4h8l4 4 4 1v3zM6 12a1.5 1.5 0 100-1M20 12a1.5 1.5 0 100-1" fill="none" stroke="#E9B94F" stroke-width="1.3"/></svg>1</span>
    </div>
    <div class="insp">Next Inspection:</div>
    <div class="insp-time">Sat 21st May 9:40 Am-10:00 Am</div>
    <div class="card-foot">
      <div class="agent"><div class="avatar"></div>Sam Porter</div>
      <div class="actions">
        <svg width="16" height="16" viewBox="0 0 16 16"><circle cx="8" cy="8" r="7" fill="none" stroke="#1F2A3C" stroke-width="1.2"/><path d="M8 4v4l3 2" fill="none" stroke="#1F2A3C" stroke-width="1.2"/></svg>
        <svg width="16" height="16" viewBox="0 0 16 16"><path d="M1 5V1h4M11 1h4v4M15 11v4h-4M5 15H1v-4M1 1l14 14M15 1L1 15" fill="none" stroke="#1F2A3C" stroke-width="1.2"/></svg>
        <svg width="18" height="14" viewBox="0 0 18 14"><rect x="1" y="1" width="16" height="12" fill="none" stroke="#1F2A3C" stroke-width="1.2"/><path d="M1 1l8 7 8-7" fill="none" stroke="#1F2A3C" stroke-width="1.2"/></svg>
      </div>
    </div>
  </article>

  <article class="card" style="left:429px">
    <div class="card-img" style="background:linear-gradient(160deg,#C9D6E3,#8C98A6 50%,#5C8FBF)" role="img" aria-label="Residential tower beside a rooftop pool"></div>
    <div class="badge">On Sale</div>
    <svg class="fav" width="18" height="18" viewBox="0 0 24 24"><path d="M12 2l3 7 7 .6-5.3 4.6 1.7 7.3L12 17.6 5.6 21.5l1.7-7.3L2 9.6 9 9z" fill="#E9B94F"/></svg>
    <h3>Kenbury</h3>
    <div class="addr"><svg width="14" height="18" viewBox="0 0 14 18"><path d="M7 1a6 6 0 00-6 6c0 4.5 6 10 6 10s6-5.5 6-10a6 6 0 00-6-6z" fill="none" stroke="#E9B94F" stroke-width="1.3"/><circle cx="7" cy="7" r="2" fill="none" stroke="#E9B94F" stroke-width="1.3"/></svg>Level 3/22 Harrow Lane...</div>
    <div class="feats">
      <span class="feat"><svg width="22" height="16" viewBox="0 0 22 16"><path d="M1 15V3M21 15V9H1M4 9V5h7v4" fill="none" stroke="#E9B94F" stroke-width="1.3"/></svg>2</span>
      <span class="feat"><svg width="22" height="16" viewBox="0 0 22 16"><path d="M1 8h20v3a4 4 0 01-4 4H5a4 4 0 01-4-4zM4 8V2h3" fill="none" stroke="#E9B94F" stroke-width="1.3"/></svg>2</span>
      <span class="feat"><svg width="26" height="14" viewBox="0 0 26 14"><path d="M1 10V7l4-1 4-4h8l4 4 4 1v3zM6 12a1.5 1.5 0 100-1M20 12a1.5 1.5 0 100-1" fill="none" stroke="#E9B94F" stroke-width="1.3"/></svg>1</span>
    </div>
    <div class="insp">Next Inspection:</div>
    <div class="insp-time">Sat 21st May 9:40 Am-10:00 Am</div>
    <div class="card-foot">
      <div class="agent"><div class="avatar"></div>Sam Porter</div>
      <div class="actions">
        <svg width="16" height="16" viewBox="0 0 16 16"><circle cx="8" cy="8" r="7" fill="none" stroke="#1F2A3C" stroke-width="1.2"/><path d="M8 4v4l3 2" fill="none" stroke="#1F2A3C" stroke-width="1.2"/></svg>
        <svg width="16" height="16" viewBox="0 0 16 16"><path d="M1 5V1h4M11 1h4v4M15 11v4h-4M5 15H1v-4M1 1l14 14M15 1L1 15" fill="none" stroke="#1F2A3C" stroke-width="1.2"/></svg>
        <svg width="18" height="14" viewBox="0 0 18 14"><rect x="1" y="1" width="16" height="12" fill="none" stroke="#1F2A3C" stroke-width="1.2"/><path d="M1 1l8 7 8-7" fill="none" stroke="#1F2A3C" stroke-width="1.2"/></svg>
      </div>
    </div>
  </article>

  <article class="card" style="left:800px">
    <div class="card-img" style="background:linear-gradient(160deg,#3E7CC8,#B8BCC2 55%,#6C6A66)" role="img" aria-label="Two-storey suburban house with double garage"></div>
    <div class="badge">On Sale</div>
    <svg class="fav" width="18" height="18" viewBox="0 0 24 24"><path d="M12 2l3 7 7 .6-5.3 4.6 1.7 7.3L12 17.6 5.6 21.5l1.7-7.3L2 9.6 9 9z" fill="#E9B94F"/></svg>
    <h3>Kenbury</h3>
    <div class="addr"><svg width="14" height="18" viewBox="0 0 14 18"><path d="M7 1a6 6 0 00-6 6c0 4.5 6 10 6 10s6-5.5 6-10a6 6 0 00-6-6z" fill="none" stroke="#E9B94F" stroke-width="1.3"/><circle cx="7" cy="7" r="2" fill="none" stroke="#E9B94F" stroke-width="1.3"/></svg>Level 3/22 Harrow Lane...</div>
    <div class="feats">
      <span class="feat"><svg width="22" height="16" viewBox="0 0 22 16"><path d="M1 15V3M21 15V9H1M4 9V5h7v4" fill="none" stroke="#E9B94F" stroke-width="1.3"/></svg>2</span>
      <span class="feat"><svg width="22" height="16" viewBox="0 0 22 16"><path d="M1 8h20v3a4 4 0 01-4 4H5a4 4 0 01-4-4zM4 8V2h3" fill="none" stroke="#E9B94F" stroke-width="1.3"/></svg>2</span>
      <span class="feat"><svg width="26" height="14" viewBox="0 0 26 14"><path d="M1 10V7l4-1 4-4h8l4 4 4 1v3zM6 12a1.5 1.5 0 100-1M20 12a1.5 1.5 0 100-1" fill="none" stroke="#E9B94F" stroke-width="1.3"/></svg>1</span>
    </div>
    <div class="insp">Next Inspection:</div>
    <div class="insp-time">Sat 21st May 9:40 Am-10:00 Am</div>
    <div class="card-foot">
      <div class="agent"><div class="avatar"></div>Sam Porter</div>
      <div class="actions">
        <svg width="16" height="16" viewBox="0 0 16 16"><circle cx="8" cy="8" r="7" fill="none" stroke="#1F2A3C" stroke-width="1.2"/><path d="M8 4v4l3 2" fill="none" stroke="#1F2A3C" stroke-width="1.2"/></svg>
        <svg width="16" height="16" viewBox="0 0 16 16"><path d="M1 5V1h4M11 1h4v4M15 11v4h-4M5 15H1v-4M1 1l14 14M15 1L1 15" fill="none" stroke="#1F2A3C" stroke-width="1.2"/></svg>
        <svg width="18" height="14" viewBox="0 0 18 14"><rect x="1" y="1" width="16" height="12" fill="none" stroke="#1F2A3C" stroke-width="1.2"/><path d="M1 1l8 7 8-7" fill="none" stroke="#1F2A3C" stroke-width="1.2"/></svg>
      </div>
    </div>
  </article>

  <!-- ABOUT -->
  <div class="photo" style="left:0;top:1354px;width:638px;height:389px;background:linear-gradient(170deg,#D9DDE2 0%,#C4C9CF 45%,#7D8A5C 80%,#5E7042 100%)" role="img" aria-label="Contemporary timber and dark-clad two-storey home on a lawn"></div>
  <div class="abs eyebrow" style="left:672px;top:1389px">About Us</div>
  <h2 class="abs heading" style="left:672px;top:1412px">Who Is Ferndale?</h2>
  <div class="abs body-copy" style="left:672px;top:1452px;width:470px">
    <p>Ferndale in Spanish means "the home, the house", buying a property is one of the most expensive expenses and important assets for people. Ferndale is a real estate company located in Kenbury, Canberra.</p>
    <p style="margin-top:13px">Being a portfolio sales agent and property manager, coupled with our high-profile international real estate experience, Ferndale is considered a market leader on the cutting edge with deep industry knowledge, ranging from landlord-tenant relationships, residential purchases.</p>
  </div>

  <!-- WHY CHOOSE -->
  <div class="abs eyebrow" style="left:61px;top:1790px">Services</div>
  <h2 class="abs heading" style="left:61px;top:1813px">Why choose us?</h2>
  <p class="abs body-copy" style="left:61px;top:1855px;width:455px">Lorem Ipsum is simply dummy text of the printing and typesetting industry. Lorem Ipsum has been the industry's standard dummy text ever since the 1500s, when an unknown printer took a galley of type and scrambled it to make a type specimen book. It has survived not only five centuries, but also the leap into electronic typesetting, remaining essentially unchanged. It was popularised in the 1960s with the release of transfer sheets containing Lorem Ipsum passages, and more recently with desktop publishing</p>
  <div class="btn-outline" style="left:59px;top:2072px">Read More</div>
  <div class="photo" style="left:562px;top:1743px;width:638px;height:390px;background:linear-gradient(135deg,#E8E3DC 0%,#D6CCBF 50%,#B8A58C 100%)" role="img" aria-label="Hands passing a house key over a desk with a small model house"></div>

  <!-- TESTIMONIALS -->
  <section class="testi">
    <div class="center eyebrow" style="top:60px">Our Testimonials</div>
    <h2 class="center heading" style="top:84px;color:var(--white)">What Our People Says</h2>
    <div class="quote-card" style="left:180px">
      <svg class="qmark" width="38" height="30" viewBox="0 0 38 30"><path d="M2 28V16C2 8 7 3 15 2v5c-4 1-6 4-6 8h6v13zM21 28V16c0-8 5-13 13-14v5c-4 1-6 4-6 8h6v13z" fill="#4F6E99"/></svg>
      <p>Very good service. Our property manager is very responsible, prompting and cares about detail. They use the system to track everything so no need to worry about miscommunication. I strongly recommend this agent.</p>
      <div class="who">Lena Marsh</div>
    </div>
    <div class="quote-card" style="left:618px">
      <svg class="qmark" width="38" height="30" viewBox="0 0 38 30"><path d="M2 28V16C2 8 7 3 15 2v5c-4 1-6 4-6 8h6v13zM21 28V16c0-8 5-13 13-14v5c-4 1-6 4-6 8h6v13z" fill="#4F6E99"/></svg>
      <p>Very good service. Our property manager is very responsible, prompting and cares about detail. They use the system to track everything so no need to worry about miscommunication. I strongly recommend this agent.</p>
      <div class="who">Lena Marsh</div>
    </div>
  </section>
  <div class="arrow" style="left:102px;background:var(--gold)"><svg width="20" height="12" viewBox="0 0 20 12"><path d="M19 6H2M7 1L2 6l5 5" fill="none" stroke="#1D2E4C" stroke-width="1.8"/></svg></div>
  <div class="arrow" style="left:1066px;background:var(--white)"><svg width="20" height="12" viewBox="0 0 20 12"><path d="M1 6h17M13 1l5 5-5 5" fill="none" stroke="#1D2E4C" stroke-width="1.8"/></svg></div>

  <!-- NEWS -->
  <div class="center eyebrow" style="top:2724px">Blog</div>
  <h2 class="center heading" style="top:2748px">Our Latest News</h2>

  <article class="post" style="left:60px">
    <div class="post-img" style="background:linear-gradient(170deg,#D8DEE6,#B9BDC2 55%,#6F7F52)" role="img" aria-label="Two-storey white home with timber cladding and garage"></div>
    <div class="meta"><span><svg width="14" height="14" viewBox="0 0 14 14"><rect x="1" y="2" width="12" height="11" fill="none" stroke="#8A8F99"/><path d="M1 5h12M4 1v2M10 1v2" stroke="#8A8F99"/></svg>15 April 2022</span><span><svg width="16" height="14" viewBox="0 0 16 14"><path d="M1 2h14v8H6l-4 3v-3H1z" fill="none" stroke="#8A8F99"/></svg>5 Comments</span></div>
    <h4>Lorem Ipsum is simply dummy text</h4>
    <p>Lorem Ipsum is simply dummy text of the printing and typesetting industry.</p>
    <div class="more">Read More ›</div>
  </article>
  <article class="post" style="left:430px">
    <div class="post-img" style="background:linear-gradient(170deg,#4A6FA8,#8A8C8E 55%,#5A5048)" role="img" aria-label="Modern glass-fronted house lit at dusk"></div>
    <div class="meta"><span><svg width="14" height="14" viewBox="0 0 14 14"><rect x="1" y="2" width="12" height="11" fill="none" stroke="#8A8F99"/><path d="M1 5h12M4 1v2M10 1v2" stroke="#8A8F99"/></svg>15 April 2022</span><span><svg width="16" height="14" viewBox="0 0 16 14"><path d="M1 2h14v8H6l-4 3v-3H1z" fill="none" stroke="#8A8F99"/></svg>5 Comments</span></div>
    <h4>Lorem Ipsum is simply dummy text</h4>
    <p>Lorem Ipsum is simply dummy text of the printing and typesetting industry.</p>
    <div class="more">Read More ›</div>
  </article>
  <article class="post" style="left:800px">
    <div class="post-img" style="background:linear-gradient(170deg,#E3E3DF,#8C9096 50%,#4E6B3E)" role="img" aria-label="Terraced townhouse facade with dark door and hedges"></div>
    <div class="meta"><span><svg width="14" height="14" viewBox="0 0 14 14"><rect x="1" y="2" width="12" height="11" fill="none" stroke="#8A8F99"/><path d="M1 5h12M4 1v2M10 1v2" stroke="#8A8F99"/></svg>15 April 2022</span><span><svg width="16" height="14" viewBox="0 0 16 14"><path d="M1 2h14v8H6l-4 3v-3H1z" fill="none" stroke="#8A8F99"/></svg>5 Comments</span></div>
    <h4>Lorem Ipsum is simply dummy text</h4>
    <p>Lorem Ipsum is simply dummy text of the printing and typesetting industry.</p>
    <div class="more">Read More ›</div>
  </article>

  <!-- FOOTER -->
  <footer class="footer">
    <div class="brand" style="top:48px;left:60px">
      <div class="brand-mark" style="width:54px;height:54px;border-color:var(--white)"></div>
      <div><div class="brand-name" style="color:var(--white);font-size:38px">Ferndale</div><div class="brand-sub" style="color:var(--white)">Estate Collective</div></div>
    </div>
    <p class="abs f-text" style="left:61px;top:117px;width:210px">Lorem ipsum dolor sit amet, consectetur adipiscing elit, sed do eiusmod tempor...</p>

    <div class="abs" style="left:331px;top:53px">
      <div class="f-title">Site Map</div>
      <ul class="f-list" style="margin-top:8px">
        <li class="active">Home</li><li>About Us</li><li>Leasing</li><li>Buy</li><li>Sell</li><li>Our Team</li><li>Blog</li><li>Contact Us</li>
      </ul>
    </div>

    <div class="abs" style="left:613px;top:53px;width:260px">
      <div class="f-title">Contact Us</div>
      <div class="f-text" style="display:flex;gap:14px;margin-top:16px"><svg width="18" height="22" viewBox="0 0 18 22"><path d="M9 1a7 7 0 00-7 7c0 5 7 12 7 12s7-7 7-12a7 7 0 00-7-7z" fill="none" stroke="#fff" stroke-width="1.2"/><circle cx="9" cy="8" r="2.5" fill="none" stroke="#fff" stroke-width="1.2"/></svg><span>210/5 Harrow Lane, Kenbury, ACT, 2999</span></div>
      <div class="f-text" style="display:flex;gap:14px;margin-top:10px;font-weight:500"><svg width="18" height="18" viewBox="0 0 18 18"><path d="M4 1l3 4-2 2c1 2 4 5 6 6l2-2 4 3-2 3C8 17 1 10 1 3z" fill="none" stroke="#fff" stroke-width="1.2"/></svg><span>02 6000 1234<br><span style="line-height:30px">02 6000 5678</span></span></div>
      <div class="f-text" style="display:flex;gap:14px;margin-top:8px"><svg width="20" height="14" viewBox="0 0 20 14"><rect x="1" y="1" width="18" height="12" fill="none" stroke="#fff" stroke-width="1.2"/><path d="M1 1l9 7 9-7" fill="none" stroke="#fff" stroke-width="1.2"/></svg><span>info@ferndaleestate.com.au</span></div>
    </div>

    <div class="abs" style="left:889px;top:53px">
      <div class="f-title">Follow On Us</div>
      <div class="social" aria-label="Social media links"><span class="fill"></span><span></span><span></span><span></span></div>
    </div>
  </footer>

  <div class="cta">
    <h2>Contact Us If You Want To Sell Your House Or You<br>Have Other Questions</h2>
    <div class="cta-btn">Contact Us Today</div>
  </div>

  <div class="legal">
    <span class="abs" style="left:61px;top:11px">2022© Ferndale Estate Collective. All right reserved.</span>
    <span class="abs" style="left:655px;top:11px">Privacy</span>
    <span class="abs" style="left:724px;top:11px">Complaint Handling &amp; Dispute Resolution</span>
    <span class="abs" style="left:998px;top:11px">Due Diligence Checklist</span>
  </div>

</div>
</body>
</html>
```